Brimora - Nutritious Snacks and Desserts

We need a creative e-commerce website in which all features--buttons, background, etc.--convey our message: We sell delicious, nutritious snacks and desserts that most closely comply with the paleo diet guidelines. Our first product is Nuttaree®--raw, vegan, paleo chocolate balls that are made of dates, coconut, and cocoa. Our products are organic, raw, irresistible and nutritious. We have several versions of Nuttaree® in development, as well as mousse, ice cream, and crackers. Our mission is to purvey basic healthy foods. Our motto is, "Fuel for the Bold Trail-Walker(tm)."

Target Market(s)

Health-conscious professionals who tend to shop at health food stores. Our products also meet the requirements of a gluten-free diet; and they also don't contain refined sugar, so shoppers with gluten and possibly sugar issues are incidental customers.

Industry/Entity Type

Health Product

Coding

Number of Pages Required

5+ page

Colors

Designer to choose colors to be used in the design.

Requirements
Must have
• We need at least a home page, a products page, an about-us page, a contact page, and a shopping cart page. We would like to be able to add products on our own later. We should be able to handle some basic coding, especially if it's just a matter of copying and modifying product pages. We would also like the ability in the future to add blogging pages, allowing us to write articles about health food and healthy lifestyle, thus attracting web-traffic (SEO).
• Other features we would like to have:
• Product photo slider on the hopepage
• Back-to-top button at the bottom of the home page
• Make sure the site is mobile-compatible
• A search bar at the top of the homepage
• "Create an account" and "Previous orders"--allowing customers to see their previous orders and reorder what they purchased in the past.
Nice to have
• We would like to convey the paleo theme without actually stating it anywhere. We'll add text as necessary, according to the page layout; you can use ipsum lorem for purpose of demonstration.

```html
<!DOCTYPE html>
<html lang="en">
<head>
<meta charset="utf-8">
<title>Brimora – Nutritious Snacks and Desserts</title>
<link rel="stylesheet" href="https://fonts.googleapis.com/css2?family=Abhaya+Libre:wght@400;500;600&display=swap">
<style>
:root{
  --lime:#6a9f02;
  --lime-bright:#9ccc1c;
  --lime-pale:#e3f6c1;
  --forest:#2c4606;
  --forest-text:#33500c;
  --ink:#333;
  --paper:#f3f3f1;
  --white:#fff;
}
*{margin:0;padding:0;box-sizing:border-box}
html,body{width:1200px;height:2590px;overflow:hidden}
body{font-family:"Abhaya Libre",Georgia,serif;color:var(--ink);background:var(--white);position:relative}
.btn{display:block;margin:0 auto;width:214px;height:41px;line-height:41px;border-radius:21px;background:var(--forest);color:var(--white);text-align:center;font-size:17px;text-decoration:none}

/* hero */
.hero{position:relative;height:627px;overflow:hidden}
.hero-photo{position:absolute;inset:0;background:radial-gradient(ellipse at 40% 40%,#8fc400 0%,#6c9c00 45%,#3f6100 100%)}
.brand-badge{position:absolute;left:498px;top:-40px;width:204px;height:204px;border-radius:50%;background:var(--white);text-align:center;padding-top:60px}
.brand-dot{display:block;width:52px;height:52px;margin:0 auto 4px;border-radius:50%;background:var(--lime-bright)}
.brand-name{font-size:32px;color:var(--lime);letter-spacing:5px;line-height:1}
.menu{position:absolute;right:50px;top:52px;color:var(--white);font-size:17px;display:flex;align-items:center;gap:16px}
.menu svg{display:block}
.hero-title{position:absolute;top:296px;width:100%;text-align:center;color:var(--white);font-size:46px;font-weight:400;line-height:48px}
.hero .btn{position:absolute;left:493px;top:400px}

/* welcome */
.welcome{height:375px;background:var(--lime);color:var(--white);text-align:center;padding-top:66px}
.welcome h2{font-size:45px;font-weight:400;line-height:54px}
.welcome p{font-size:16px;line-height:26px;width:800px;margin:30px auto 0}
.welcome .tagline{font-size:23px;margin-top:14px}
.welcome .btn{margin-top:28px}

/* about */
.about{position:relative;height:843px;text-align:center}
.section-title{font-size:46px;font-weight:400;color:var(--forest-text);line-height:54px}
.about .section-title{padding-top:44px}
.about-ring{position:absolute;left:0;top:0}
.feature{position:absolute;width:200px;text-align:center;color:var(--forest-text);font-size:17px;line-height:20px}
.feature svg{display:block;margin:0 auto 12px}
.product-hero{position:absolute;left:441px;top:1309px}
.about-copy{position:absolute;top:628px;width:100%;font-size:13px;line-height:18px;color:#444}
.about .btn{position:absolute;left:493px;top:741px}

/* products */
.products{height:564px;background:var(--paper);text-align:center;padding-top:30px;position:relative}
.product-grid{position:absolute;top:106px;left:0;width:100%}
.product{position:absolute;width:300px;text-align:center}
.product-image{width:260px;height:260px;margin:0 auto;border-radius:50%;border:8px solid var(--lime-bright);background:radial-gradient(circle at 50% 45%,#c89a6c 0%,#9c6c43 60%,#6e4627 100%)}
.product-name{font-size:22px;font-weight:400;color:#222;margin-top:14px;line-height:26px}
.product-desc{font-size:13px;line-height:18px;color:#444;width:240px;margin:6px auto 0}
.price{font-size:31px;color:#222;margin-top:4px;line-height:38px}
.product .btn{width:155px;height:31px;line-height:31px;font-size:16px;margin-top:4px}

/* footer */
.site-footer{height:181px;background:var(--lime-pale);border-top:4px solid var(--lime);text-align:center;padding-top:22px}
.site-footer .brand-dot{width:56px;height:56px}
.site-footer .brand-name{font-size:36px}
.copyright{font-size:11px;color:#333;margin-top:10px}
</style>
</head>
<body>

<header class="hero">
  <div class="hero-photo" role="img" aria-label="Fresh vegetables, fruit and fish toned in bright lime green"></div>
  <div class="brand-badge"><span class="brand-dot"></span><span class="brand-name">brimora</span></div>
  <nav class="menu">Menu
    <svg width="26" height="18" viewBox="0 0 26 18"><g stroke="#fff" stroke-width="2"><line x1="0" y1="1" x2="26" y2="1"/><line x1="0" y1="9" x2="26" y2="9"/><line x1="0" y1="17" x2="26" y2="17"/></g></svg>
  </nav>
  <h1 class="hero-title">Fuel for the Bold<br>Trail-Walker™</h1>
  <a class="btn" href="#">Learn More</a>
</header>

<section class="welcome">
  <h2>Welcome to Brimora Foods</h2>
  <p>Our products are raw, organic, vegan, gluten-free, dairy-free, fiber-rich, nutrient-dense, antioxidant-rich real foods with no preservatives, no added sugar, and no artificial or plant-based sweeteners.</p>
  <p class="tagline">And they are irresistibly scrumptious!</p>
  <a class="btn" href="#">Learn More</a>
</section>

<section class="about">
  <h2 class="section-title">About Us</h2>
  <svg class="about-ring" width="1200" height="843" viewBox="0 0 1200 843">
    <path d="M370 312 A294 294 0 0 1 830 312" fill="none" stroke="#d6f0a8" stroke-width="2"/>
    <circle cx="600" cy="464" r="159" fill="none" stroke="#d6f0a8" stroke-width="3"/>
  </svg>
  <div class="feature" style="left:500px;top:120px">
    <svg width="60" height="60" viewBox="0 0 60 60" fill="none" stroke="#7fb800" stroke-width="2.5"><path d="M12 22 A18 18 0 0 1 48 22"/><circle cx="30" cy="38" r="18"/><path d="M30 52 C20 44 22 30 30 26 C38 30 40 44 30 52Z"/><line x1="30" y1="30" x2="30" y2="52"/></svg>
    Raw
  </div>
  <div class="feature" style="left:237px;top:312px">
    <svg width="60" height="70" viewBox="0 0 60 70" fill="none" stroke="#7fb800" stroke-width="2.5"><ellipse cx="18" cy="12" rx="8" ry="10"/><line x1="18" y1="22" x2="18" y2="66"/><path d="M34 2 v14 a6 6 0 0 0 12 0 V2 M40 2 v64"/><path d="M30 60 C30 44 46 40 56 44 C56 58 44 64 30 60Z"/></svg>
    Organic
  </div>
  <div class="feature" style="left:751px;top:312px">
    <svg width="60" height="70" viewBox="0 0 60 70" fill="none" stroke="#7fb800" stroke-width="2.5"><rect x="10" y="18" width="40" height="48"/><path d="M18 18 v-8 M26 18 v-12 M34 18 v-10 M42 18 v-6"/><path d="M30 56 C20 50 22 38 30 36 C38 38 40 50 30 56Z"/></svg>
    Irresistible<br>&amp; Nutritious.
  </div>
  <div role="img" aria-label="Nuttaree® package lid with a raw chocolate ball" style="position:absolute;left:479px;top:343px;width:242px;height:242px;border-radius:50%;background:radial-gradient(circle at 50% 45%,#c89a6c 0%,#9c6c43 60%,#6e4627 100%);box-shadow:0 10px 24px rgba(0,0,0,.25)"></div>
  <p class="about-copy">Sed ut perspiciatis unde omnis iste natus error sit voluptatem accusantium doloremque laudantium, totam rem aperiam,<br>eaque ipsa quae ab illo inventore veritatis et quasi architecto beatae vitae dicta sunt explicabo.<br>Nemo enim ipsam voluptatem quia voluptas sit aspernatur aut odit aut fugit, sed quia consequuntur magni dolores eos qui<br>ratione voluptatem sequi nesciunt. Neque porro quisquam est, qui dolorem ipsum quia dolor sit amet, consectetur</p>
  <a class="btn" href="#">Read More</a>
</section>

<section class="products">
  <h2 class="section-title">Product</h2>
  <div class="product-grid">
    <article class="product" style="left:92px">
      <div class="product-image" role="img" aria-label="Nuttaree® mousse package lid"></div>
      <h3 class="product-name">Mousse</h3>
      <p class="product-desc">Sed ut perspiciatis unde omnis iste natus error sit voluptatem</p>
      <p class="price">$6.00</p>
      <a class="btn" href="#">View Details</a>
    </article>
    <article class="product" style="left:450px">
      <div class="product-image" role="img" aria-label="Nuttaree® ice cream package lid"></div>
      <h3 class="product-name">Ice Cream</h3>
      <p class="product-desc">Sed ut perspiciatis unde omnis iste natus error sit voluptatem</p>
      <p class="price">$10.00</p>
      <a class="btn" href="#">View Details</a>
    </article>
    <article class="product" style="left:812px">
      <div class="product-image" role="img" aria-label="Nuttaree® crackers package lid"></div>
      <h3 class="product-name">Crackers</h3>
      <p class="product-desc">Sed ut perspiciatis unde omnis iste natus error sit voluptatem</p>
      <p class="price">$12.00</p>
      <a class="btn" href="#">View Details</a>
    </article>
  </div>
</section>

<footer class="site-footer">
  <span class="brand-dot"></span>
  <div class="brand-name">brimora</div>
  <p class="copyright">© 2018 Company Name | All Rights Reserved</p>
</footer>

</body>
</html>
```